Marwick Law Letterhead

We need a new letterhead design for a Law Firm. The address for the law firm is 1475 Calloway Street, Suite 210, Houston, Texas 77041. Phone Number: 832-361-9027; Fax Number: 832-614-7359. The logo is uploaded to the project.

```html
<!DOCTYPE html>
<html lang="en">
<head>
<meta charset="utf-8">
<title>Marwick Law Letterhead</title>
<link rel="stylesheet" href="https://fonts.googleapis.com/css2?family=Montserrat:wght@400;500&display=swap">
<style>
:root{
  --bg:#e8e8e8;
  --paper:#ffffff;
  --navy:#1b2d5c;
  --red:#e01a22;
  --deep-red:#5e0008;
  --ink:#2a2a2a;
  --ink-dark:#111111;
}
*{margin:0;padding:0;box-sizing:border-box}
html,body{width:1154px;height:1200px;overflow:hidden;background:var(--bg)}
body{font-family:"Montserrat",Arial,sans-serif;color:var(--ink)}
.letterhead{position:absolute;left:158px;top:15px;width:837px;height:1170px;background:var(--paper);box-shadow:0 4px 18px rgba(0,0,0,.18)}
.brand{position:absolute;left:33px;top:78px;display:flex;align-items:center;gap:12px}
.brand-mark{width:34px;height:34px;background:var(--navy)}
.brand-name{font-size:30px;font-weight:500;color:var(--navy);letter-spacing:.5px}
.contact{position:absolute;left:614px;top:57px;height:97px;border-left:1.5px solid var(--red);padding-left:21px;font-size:14px;line-height:18px;color:var(--ink-dark)}
.contact-address{margin-top:3px}
.contact-line{display:flex;align-items:center;gap:8px;margin-top:3px}
.contact-address + .contact-line{margin-top:12px}
.contact-line svg{width:14px;height:14px}
.recipient{position:absolute;left:31px;top:272px;font-size:13.6px;line-height:20.8px;color:var(--ink-dark)}
.body-copy{position:absolute;left:33px;top:357px;width:775px;font-size:13.6px;line-height:20.8px;text-align:justify}
.body-copy p + p{margin-top:20.8px}
.closing{position:absolute;left:30px;top:944px;font-size:16.5px;color:var(--ink-dark)}
.signature{position:absolute;left:30px;top:975px;width:92px;height:26px;background:linear-gradient(90deg,#3a3a3a22,#11111133);border-radius:3px}
.footer-band{position:absolute;left:0;bottom:0;width:100%;height:29px;display:flex}
.footer-band-red{width:672px;background:linear-gradient(90deg,var(--red),var(--deep-red))}
.footer-band-gap{width:5px;background:var(--paper)}
.footer-band-navy{flex:1;background:var(--navy)}
</style>
</head>
<body>
<main class="letterhead">
  <header>
    <div class="brand">
      <span class="brand-mark"></span>
      <span class="brand-name">Marwick Law</span>
    </div>
    <address class="contact" style="font-style:normal">
      <div class="contact-address">1475 Calloway Street,<br>Suite 210, Houston,<br>Texas 77041</div>
      <div class="contact-line">
        <svg viewBox="0 0 24 24" aria-hidden="true"><path fill="var(--red)" d="M6.6 10.8a15 15 0 0 0 6.6 6.6l2.2-2.2a1 1 0 0 1 1-.25 11.4 11.4 0 0 0 3.6.57 1 1 0 0 1 1 1V20a1 1 0 0 1-1 1A17 17 0 0 1 3 4a1 1 0 0 1 1-1h3.5a1 1 0 0 1 1 1c0 1.25.2 2.45.57 3.57a1 1 0 0 1-.25 1z"/></svg>
        <span>832-361-9027</span>
      </div>
      <div class="contact-line">
        <svg viewBox="0 0 24 24" aria-hidden="true"><path fill="var(--red)" d="M7 3h10v4H7zM4 8h16a2 2 0 0 1 2 2v6h-4v5H6v-5H2v-6a2 2 0 0 1 2-2zm4 7v4h8v-4z"/></svg>
        <span>832-614-7359</span>
      </div>
    </address>
  </header>

  <section class="recipient">
    <div>Mr/s</div>
    <div>First Name and Last Name</div>
    <div>Company Name</div>
    <div>Address</div>
  </section>

  <section class="body-copy">
    <p>Lorem ipsum dolor sit amet,consectetur adipiscing sed do eiusmod tempor incididunt laboreet dolore magna aliqua.Ut enim ad minim.veniam, quis nostrud exercitation ullamco laboris nisi ut aliquip exea commodo consequat.Lorem ipsum dolor sit amet,consectetur adipiscing sed do eiusmod tempor incididunt.labore et dolore magna aliqua. Ut enim</p>
    <p>Lorem ipsum dolor sit amet, consectetur adipiscing sed do eiusmod tempor incididunt labore et dolore magna aliqua. Ut enim ad minim veniam, quis nostrud exercitation ullamco laboris nisi ut aliquip exea commodo consequat.Duis aute irure dolor in reprehenderit in voluptate velit esse cillum irure dolor in reprehenderit in voluptate velit esse irure</p>
    <p>Lorem ipsum dolor sit amet, consectetur adipiscing sed do eiusmod tempor incididunt labore et dolore magna aliqua. consequat. Duis aute irure dolor in.reprehenderit in voluptate velit esse cillum dolore eu fugiat nulla pariatur. Excepteur sint occaecat cupidatat non proident, sunt in culpa qui officia deserunt mollit,</p>
    <p>Lorem ipsum dolor sit amet, consectetur adipiscing sed do eiusmod tempor incididunt labore et dolore magna aliqua. Ut enim Lorem ipsum dolor sit amet, consectetur adipiscing sed do eiusmod tempor incididunt labore et dolore magna aliqua. Ut enim Lorem ipsum aliqua.ipsum</p>
    <p>Lorem ipsum dolor sit amet, consectetur adipiscing sed do eiusmod tempor incididunt labore et dolore magna aliqua. Ut enim ad minim veniam, quis nostrud exercitation ullamco laboris nisi ut aliquip exea commodo consequat.Duis aute irure dolor in reprehenderit in voluptate velit esse cillum irure dolor in reprehenderit in voluptate velit esse irure</p>
    <p>Lorem ipsum dolor sit amet, consectetur adipiscing sed do eiusmod tempor incididunt labore et dolore magna aliqua. Ut enim ad minim veniam, quis nostrud exercitation ullamco laboris nisi ut aliquip exea commodo consequat.Duis aute irure dolor in reprehenderit in voluptate velit esse cillum irure dolor in reprehenderit in voluptate velit esse irure</p>
  </section>

  <div class="closing">Regards</div>
  <div class="signature" role="img" aria-label="Handwritten signature of the sender"></div>

  <footer class="footer-band">
    <div class="footer-band-red"></div>
    <div class="footer-band-gap"></div>
    <div class="footer-band-navy"></div>
  </footer>
</main>
</body>
</html>
```